National Mission Critical Construction Contractor needs Stationery Design to make a bold statement

We are a small commercial construction company, working primarily in mission critical facilities across the U.S.. We have exciting corporate changes going an and a new logo and office space so we need new stationery. The final design should incorporate our new logo and invoke a fresh, high-tech feel while looking simple and modern.

Industry/Entity Type

Construction

Contact Information for Business Card

We are required to list our state licensing qualifications on the back of our card.

Font styles to use
Sans Serif

Requirements
Must have
• We need to have a design for second page of stationery, envelopes both standard and with a window and for a 3 x 4 notepad.

```html
<!DOCTYPE html>
<html lang="en">
<head>
<meta charset="utf-8">
<title>Northcrest Business Card</title>
<link href="https://fonts.googleapis.com/css2?family=Open+Sans:wght@400;600&display=swap" rel="stylesheet">
<style>
  :root {
    --page-bg: #e9ebee;
    --blue-deep: #0b3a86;
    --blue-mid: #2a64bd;
    --blue-light: #4d88d8;
    --frost-1: #eef1f4;
    --frost-2: #d9dee4;
    --navy: #14305e;
    --text-light: #e8eef8;
    --text-soft: #c6d4ea;
  }
  * { margin: 0; padding: 0; box-sizing: border-box; }
  html, body {
    width: 1200px; height: 969px; overflow: hidden;
    background: var(--page-bg);
    font-family: "Open Sans", sans-serif;
  }
  .card {
    position: absolute; left: 100px; top: 199px;
    width: 1000px; height: 571px;
    background: linear-gradient(135deg, var(--frost-1), var(--frost-2));
    box-shadow: 0 10px 30px rgba(0,0,0,0.18);
    overflow: hidden;
  }
  .card-shape { position: absolute; inset: 0; width: 1000px; height: 571px; }
  .contact { position: absolute; left: 45px; top: 0; color: var(--text-light); }
  .contact .name { position: absolute; top: 78px; font-size: 31px; font-weight: 600; white-space: nowrap; }
  .contact .role { position: absolute; top: 122px; font-size: 25px; color: var(--text-soft); }
  .address { position: absolute; top: 210px; font-size: 24px; line-height: 34px; white-space: nowrap; color: var(--text-soft); }
  .lines { position: absolute; top: 296px; list-style: none; }
  .lines li { display: flex; align-items: center; height: 39px; font-size: 24px; color: var(--text-soft); white-space: nowrap; }
  .lines svg { width: 26px; height: 26px; margin-right: 24px; fill: var(--text-soft); }
  .brand {
    position: absolute; left: 540px; top: 180px; width: 340px;
    display: flex; flex-direction: column; align-items: center;
  }
  .brand-mark { width: 84px; height: 84px; border: 5px solid var(--navy); border-radius: 50%; }
  .brand-name {
    margin-top: 40px; font-size: 50px; font-weight: 400; letter-spacing: 2px;
    color: var(--navy); text-transform: uppercase;
  }
</style>
</head>
<body>
  <div class="card">
    <svg class="card-shape" viewBox="0 0 1000 571" aria-hidden="true">
      <defs>
        <linearGradient id="panelBlue" x1="0" y1="0" x2="1" y2="1">
          <stop offset="0" stop-color="var(--blue-light)"/>
          <stop offset="0.45" stop-color="var(--blue-mid)"/>
          <stop offset="1" stop-color="var(--blue-deep)"/>
        </linearGradient>
      </defs>
      <path d="M0 0 H500 C400 140 380 380 630 571 H0 Z" fill="url(#panelBlue)"/>
      <path d="M500 0 C400 140 380 380 630 571 H660 C420 390 440 140 540 0 Z" fill="var(--blue-deep)" opacity="0.85"/>
      <path d="M512 0 C418 150 410 380 648 571" fill="none" stroke="#ffffff" stroke-width="2" opacity="0.8"/>
    </svg>

    <div class="contact">
      <p class="name">Mark Ellison</p>
      <p class="role">President</p>
      <p class="address">2140 Harbor Lane<br>Millbrook, NY 12545</p>
      <ul class="lines">
        <li><svg viewBox="0 0 24 24"><path d="M3 9c0-3 4-5 9-5s9 2 9 5l-4 1-1-3H8L7 10zM6 12h12l2 8H4z"/></svg>555 0142 7781</li>
        <li><svg viewBox="0 0 24 24"><path d="M7 2h10a1 1 0 0 1 1 1v18a1 1 0 0 1-1 1H7a1 1 0 0 1-1-1V3a1 1 0 0 1 1-1zm1 3v13h8V5z"/></svg>555 0198 3364</li>
        <li><svg viewBox="0 0 24 24"><path d="M7 3h10v5H7zM4 9h16v8h-3v4H7v-4H4zm5 6v4h6v-4z"/></svg>555 0176 2209</li>
        <li><svg viewBox="0 0 24 24"><path d="M3 6h18v12H3zm2 2v1l7 4 7-4V8l-7 4z"/></svg>mark@northcrest.com</li>
        <li><svg viewBox="0 0 24 24"><path d="M12 2a10 10 0 1 0 0 20 10 10 0 0 0 0-20zm-1 3 3 3-2 2 3 3-1 4-4-3 1-3-4-2 2-3z"/></svg>www.northcrest.com</li>
      </ul>
    </div>

    <div class="brand">
      <div class="brand-mark"></div>
      <p class="brand-name">Northcrest</p>
    </div>
  </div>
</body>
</html>
```